Hull Harbour Trade Website makeover

Hull Harbour Trade is in need of a makeover. It is feeling tired and needs a fresh new look and feel as well as being user friendly.

Hull Harbour Trade is an industry owned marketplace website for the sale of recreational boats, marina berths, chandlery, water craft like kayaks - anything related to recreation on the water. The main focus however is boats - new and used. The site is only available to industry businesses so no private sales are available on the site.

This approach ensures that the buyers know that title is guaranteed to all boats sold and that the businesses are reputable and stand behind their products.

The current site address is www.hullharbourtrade.com.au

Target Market(s)

The target market are people interested in outdoor recreation - boaters, kayakers, sailors, paddle boarders, those looking for marina berths for their boat and those looking for service providers.

It should appeal to families, males and females, sports oriented people, fishermen, and those just looking for a relaxing, outdoor, healthy lifestyle.

Requirements
Must have
• Be very user friendly, intuitive in terms of searching, be uncluttered, fresh and engaging.
• Marine recreation is about lifestyle, fun and relaxation. When people buy a boat they are buying into a desirable, healthy lifestyle.
• It must present as professional and give consumers confidence about the professionalism of the businesses selling their products on the site.
Nice to have
• Good images that portray the lifestyle in the Australian marketplace.
• Cater for the needs of sellers to be able to showcase their products to consumers.
Should not have
• Be cluttered and hard to navigate.

```html
<!DOCTYPE html>
<html lang="en">
<head>
<meta charset="utf-8">
<title>Hull Harbour Trade</title>
<link href="https://fonts.googleapis.com/css2?family=Open+Sans:wght@400;600;700;800&display=swap" rel="stylesheet">
<style>
:root{
  --navy:#1d4a7e;
  --blue:#1f6fb5;
  --sky:#4aa3dc;
  --pale:#d6e8f5;
  --page:#e8edf1;
  --text:#3b4650;
  --muted:#7c8791;
  --white:#ffffff;
}
*{box-sizing:border-box;margin:0;padding:0}
html,body{width:686px;height:1200px;overflow:hidden}
body{font-family:"Open Sans",Arial,sans-serif;background:var(--page);color:var(--text);font-size:7px;line-height:1.35}
.site{width:686px;height:1200px;position:relative}
.header{height:42px;background:var(--white);display:flex;align-items:center;justify-content:space-between;padding:0 24px}
.brand{display:flex;align-items:center;gap:6px;font-weight:800;font-size:19px;color:var(--blue)}
.brand-mark{width:16px;height:16px;background:var(--blue);border-radius:3px}
.phone{display:flex;align-items:center;gap:6px;font-size:15px;font-weight:700;color:var(--navy)}
.phone-icon{width:18px;height:18px;border-radius:50%;background:var(--blue);display:flex;align-items:center;justify-content:center}
.nav{height:16px;background:var(--navy);display:flex;align-items:center;gap:11px;padding:0 24px}
.nav a{color:var(--white);text-decoration:none;font-size:6.5px;font-weight:600}
.hero{height:252px;position:relative;background:linear-gradient(180deg,#8cc3ea 0%,#bfdcf0 45%,#2d77b3 62%,#1a5a93 100%)}
.hero-tagline{position:absolute;left:24px;top:24px;display:flex;flex-direction:column;gap:3px;align-items:flex-start}
.hero-tagline span{background:rgba(20,50,90,.75);color:var(--white);font-size:12px;font-weight:700;padding:2px 6px}
.hero-tagline .accent{color:#9fd8ff}
.hero-dots{position:absolute;right:22px;bottom:8px;display:flex;gap:4px}
.hero-dots i{width:5px;height:5px;border-radius:50%;background:rgba(255,255,255,.6)}
.hero-dots i:first-child{background:var(--white)}
.search{margin:10px 24px 0;height:78px;background:linear-gradient(180deg,#e6f2fb,var(--pale));border:1px solid #b9d4ea;display:flex;padding:8px 10px;gap:14px}
.search-block{flex:1}
.search-block h2{font-size:11px;font-weight:700;color:var(--white);background:var(--sky);padding:3px 8px;margin-bottom:6px}
.fields{display:flex;gap:5px}
.field{height:13px;background:var(--white);border:1px solid #aac3d8;flex:1;min-width:0;font-size:6px;color:var(--muted);padding:2px 4px}
.btn{display:inline-block;background:var(--navy);color:var(--white);font-size:7px;font-weight:700;padding:3px 9px;text-transform:uppercase;white-space:nowrap}
.btn.light{background:var(--blue)}
.row{display:flex;gap:5px;margin-top:6px;align-items:center}
.main{margin:10px 24px 0;display:flex;gap:12px;height:525px}
.content{flex:1;background:var(--white)}
.sidebar{width:186px;display:flex;flex-direction:column;gap:10px}
.section-title{background:var(--sky);color:var(--white);font-size:10px;font-weight:700;padding:3px 10px}
.intro{padding:8px 10px}
.intro p{margin-bottom:6px;font-size:6.5px}
.more{text-align:right}
.more .btn{text-transform:lowercase}
.listing{display:flex;gap:10px;padding:12px 10px;border-bottom:1px solid #e2e7eb}
.listing-media{width:128px;flex-shrink:0}
.listing-photo{height:96px;background:linear-gradient(180deg,#9ccbeb,#f2f6f9 55%,#2f79b2)}
.listing-caption{background:var(--navy);color:var(--white);font-weight:700;font-size:7.5px;padding:3px 5px}
.listing-body{flex:1;display:flex;gap:8px}
.listing-body div{flex:1}
.price{color:var(--navy);font-weight:700;font-size:8px;margin-bottom:2px}
.listing-body p{font-size:6px}
.view{color:var(--blue);font-weight:700;font-size:6.5px;margin-top:3px}
.panel{background:var(--white)}
.panel-body{padding:7px 8px}
.news-item{margin-bottom:7px;font-size:6px}
.news-item b{color:var(--navy);display:block}
.weather{height:62px;background:linear-gradient(180deg,#eef5fb,#d4e6f4);border:1px solid #bed6ea;margin-top:4px;padding:4px;font-size:6px;color:var(--navy)}
.weather-bars{display:flex;gap:3px;align-items:flex-end;height:34px;margin-top:4px}
.weather-bars i{flex:1;background:var(--sky)}
.register h3{font-size:11px;color:var(--navy);font-weight:800;margin-bottom:4px}
.register-photo{height:50px;background:linear-gradient(180deg,#a7d2ef,#3d85bf);margin-top:6px}
.ads{margin:10px 24px 0;display:flex;gap:8px;height:92px}
.ad{flex:1;display:flex;flex-direction:column}
.ad-photo{flex:1;background:linear-gradient(180deg,#5fa7da,#1e5d96)}
.ad-phone{background:var(--white);color:var(--navy);font-size:10px;font-weight:800;text-align:center;padding:3px 0}
.partners{margin:10px 24px 0;height:52px;background:var(--white);display:flex;align-items:center;justify-content:space-around;padding:0 14px}
.partners i{width:62px;height:28px;background:#cfdbe5;border-radius:3px}
.footer{position:absolute;left:0;right:0;bottom:0;height:40px;background:var(--navy);display:flex;align-items:center;justify-content:space-between;padding:0 24px;color:#c9d8e8;font-size:6.5px}
.social{display:flex;gap:4px}
.social i{width:12px;height:12px;background:#3c6ea6;border-radius:2px}
</style>
</head>
<body>
<div class="site">
  <header class="header">
    <div class="brand"><span class="brand-mark"></span>Hull Harbour Trade</div>
    <div class="phone">
      <span class="phone-icon"><svg width="10" height="10" viewBox="0 0 24 24"><path fill="#fff" d="M6.6 10.8a15 15 0 0 0 6.6 6.6l2.2-2.2c.3-.3.7-.4 1-.2 1.1.4 2.3.6 3.6.6.6 0 1 .4 1 1V20c0 .6-.4 1-1 1A17 17 0 0 1 3 4c0-.6.4-1 1-1h3.5c.6 0 1 .4 1 1 0 1.3.2 2.5.6 3.6.1.3 0 .7-.2 1z"/></svg></span>
      1300 555 014
    </div>
  </header>
  <nav class="nav">
    <a>Home</a><a>New Boats</a><a>Used Boats</a><a>Marine Accessories</a><a>Marine Products &amp; Services</a><a>Accredited Brokers &amp; Dealers</a><a>Members</a><a>Marinas &amp; Berths</a><a>Useful Links</a>
  </nav>
  <section class="hero" role="img" aria-label="Large white motor yacht cruising on blue water under a clear sky">
    <div class="hero-tagline">
      <span>The ONLY</span>
      <span class="accent">ONLINE MARKETING MARKETPLACE</span>
      <span>Operated and backed by the Marine</span>
      <span>Trade Guilds*</span>
    </div>
    <div class="hero-dots"><i></i><i></i><i></i><i></i></div>
  </section>
  <section class="search">
    <div class="search-block">
      <h2>New and Used Boats for Sale</h2>
      <div class="fields"><span class="field">Boat type</span><span class="field">All Makes</span></div>
      <div class="row"><span class="field">Keyword</span><span class="btn">Quick Search</span></div>
    </div>
    <div class="search-block">
      <h2>OR select your state, a price range and new/used</h2>
      <div class="fields"><span class="field">State</span><span class="field">Price from</span><span class="field">Price to</span></div>
      <div class="row"><span class="field">New / Used</span><span class="btn">Search</span><span class="btn light">Clear</span></div>
    </div>
  </section>
  <div class="main">
    <main class="content">
      <h2 class="section-title">Boats for Sale backed by the Marine Trade Guild</h2>
      <div class="intro">
        <p>The Marine Trade Guilds and their network of members welcome you to the only marine market place where buyers can browse the widest range of boats for sale and other marine related products, backed by the guild's quality assurance program.</p>
        <p>When you deal with the professionals of the marine industry you are assured of the highest possible standard of service and product quality. All listed marine retailers are bound by a code of conduct and ethics set down by their trade guild.</p>
        <p>HullHarbourTrade.com.au is owned and operated by the Marine Trade Guilds of Australia and offers the consumer the benefit of making their purchase with the utmost confidence, from expert marine licensed members, offering quality products and service. Buy with confidence.</p>
        <p>You have come to the right place. Browse new and used boats for sale including fishing boats, power boats, sailing boats, catamarans, trimarans, runabouts, trailer sailers, cruisers, ocean yachts and more.</p>
        <div class="more"><span class="btn">learn more</span></div>
      </div>
      <h2 class="section-title">Latest Listings</h2>
      <article class="listing">
        <div class="listing-media">
          <div class="listing-photo" role="img" aria-label="Flybridge motor cruiser moored at a marina"></div>
          <div class="listing-caption">Coastline 50' Flybridge</div>
        </div>
        <div class="listing-body">
          <div><p class="price">Price: AU $235,000</p><p>Description:<br>Renowned cruising flybridge with roomy saloon, galley and two cabins. Kept in marina, serviced yearly, ready to go with full equipment list and survey report on hand.</p><p class="view">View Details &gt;</p></div>
          <div><p>Engine: Twin 375 Diesel<br>Location: Gold Coast QLD<br>Length: 50' - 15.2m<br>Hull Material: Fibreglass<br>Berth: Marina pen available<br>Accommodation: Six berths</p></div>
        </div>
      </article>
      <article class="listing">
        <div class="listing-media">
          <div class="listing-photo" role="img" aria-label="Classic trawler style cruiser on open water"></div>
          <div class="listing-caption">COASTLINE 42 CLASSIC</div>
        </div>
        <div class="listing-body">
          <div><p class="price">Price: AU $235,000</p><p>Description:<br>Well kept classic trawler with teak interior, large aft deck and walkaround decks. Economical and comfortable for long coastal passages with family and friends.</p><p class="view">View Details &gt;</p></div>
          <div><p>Engine: Twin 210 Diesel<br>Location: Sanctuary Cove QLD<br>Length: 42' - 12.8m<br>Hull Material: Fibreglass<br>Berth: Swing mooring<br>Accommodation: Four berths</p></div>
        </div>
      </article>
    </main>
    <aside class="sidebar">
      <section class="panel">
        <h2 class="section-title">Latest News</h2>
        <div class="panel-body">
          <div class="news-item"><b>10-11-13 News</b>Members invited to the spring marine expo, with new models on show and free entry for families.</div>
          <div class="news-item"><b>10-11-13 News</b>Safety week reminds owners to check flares, life jackets and radios before the holiday season.</div>
          <div class="news-item"><b>10-11-13 News</b>New marina berths open on the coast with trade discounts for listed members.</div>
        </div>
      </section>
      <section class="panel">
        <h2 class="section-title">Change Location</h2>
        <div class="panel-body">
          <div class="weather">Wind &amp; Wave Forecast<div class="weather-bars"><i style="height:40%"></i><i style="height:65%"></i><i style="height:50%"></i><i style="height:80%"></i><i style="height:60%"></i><i style="height:35%"></i></div></div>
        </div>
      </section>
      <section class="panel register">
        <h2 class="section-title">Register Now!</h2>
        <div class="panel-body">
          <h3>Want us to do the searching for you?</h3>
          <span class="btn">Register for Email Alerts</span>
          <div class="register-photo" role="img" aria-label="Couple relaxing on the deck of a boat"></div>
        </div>
      </section>
    </aside>
  </div>
  <section class="ads">
    <div class="ad"><div class="ad-photo" role="img" aria-label="Dealer advert showing new and used boats"></div><div class="ad-phone">07 5550 1184</div></div>
    <div class="ad"><div class="ad-photo" role="img" aria-label="Marina advert with boats at berth"></div><div class="ad-phone">07 5550 2276</div></div>
    <div class="ad"><div class="ad-photo" role="img" aria-label="Marine services advert with cruiser at sea"></div><div class="ad-phone">07 3550 4419</div></div>
    <div class="ad"><div class="ad-photo" role="img" aria-label="Boat broker advert with yacht on water"></div><div class="ad-phone">07 5550 1184</div></div>
  </section>
  <section class="partners"><i></i><i></i><i></i><i></i><i></i><i></i></section>
  <footer class="footer">
    <div class="social"><i></i><i></i><i></i><i></i></div>
    <span>© 2013 HullHarbourTrade.com.au. All Rights Reserved</span>
  </footer>
</div>
</body>
</html>
```